Mobile Fitness snd Therapy Business Card Design

I need a business card designed for my mobile fitness and therapy business.

Please view the images that I have uploaded. I like the simplicity of the design that I have attached. I adapted it with my information

Target Market(s)

Those seeking personal training, injury rehabilitation or massage therapy.

Industry/Entity Type

Business

Contact Information for Business Card

Derek Fulham - BKin, CEP, RMT, NSCA-CPT, Pn1
e-mail: derek@vantrelo.com
website: www.vantrelo.com
instagram: @derek_fulham

Font styles to use
Sans Serif

Colors
3176b5
0355a3

Requirements
Must have
• "Contact us to receive a FREE assessment"
• Services offered:
• Personal Training
• Golf Fitness
• Injury Rehab
• Massage Therapy
• Yoga
Nice to have
• Consistent colours with brand
• - Dark Blue: #232837
• - Blue: #5096f0
• Consistent look/feel with the website: www.vantrelo.com

```html
<!DOCTYPE html>
<html lang="en">
<head>
<meta charset="utf-8">
<title>Vantrelo Business Card</title>
<link rel="stylesheet" href="https://fonts.googleapis.com/css2?family=Montserrat:wght@500;600;700&family=Open+Sans:wght@400;600&display=swap">
<style>
  :root {
    --navy: #232837;
    --blue: #3176b5;
    --blue-deep: #0355a3;
    --blue-light: #5096f0;
    --white: #ffffff;
    --page: #ebe8e3;
    --text: #1f2330;
  }
  html, body {
    margin: 0;
    padding: 0;
    width: 1200px;
    height: 1000px;
    overflow: hidden;
    background: var(--page);
  }
  .canvas {
    position: relative;
    width: 1200px;
    height: 1000px;
  }
  .card {
    position: absolute;
    left: 266px;
    width: 666px;
    height: 397px;
    box-sizing: border-box;
    box-shadow: 0 4px 14px rgba(0,0,0,0.18);
  }
  .card--front { top: 74px; background: var(--white); }
  .card--back { top: 533px; background: var(--navy); }

  .wordmark {
    position: absolute;
    left: 0;
    width: 100%;
    text-align: center;
    font-family: "Montserrat", sans-serif;
    font-weight: 600;
    letter-spacing: 5px;
    line-height: 1;
  }
  .card--front .wordmark { top: 52px; font-size: 50px; color: var(--navy); }
  .card--back .wordmark { top: 162px; font-size: 56px; color: var(--white); }

  .tagline {
    position: absolute;
    left: 0;
    width: 100%;
    text-align: center;
    font-family: "Montserrat", sans-serif;
    font-weight: 700;
    line-height: 1;
  }
  .card--front .tagline { top: 106px; font-size: 15px; letter-spacing: 3.2px; color: var(--navy); }
  .card--back .tagline { top: 225px; font-size: 18px; letter-spacing: 3.6px; color: var(--white); }

  .side-band {
    position: absolute;
    top: 171px;
    width: 13px;
    height: 139px;
    background: var(--navy);
  }
  .side-band--left { left: 0; }
  .side-band--right { right: 0; }

  .person {
    position: absolute;
    left: 80px;
    top: 170px;
  }
  .person__name {
    margin: 0;
    font-family: "Montserrat", sans-serif;
    font-weight: 700;
    font-size: 20px;
    color: var(--navy);
    line-height: 24px;
  }
  .person__creds {
    margin: 2px 0 0;
    font-family: "Open Sans", sans-serif;
    font-size: 16px;
    color: var(--blue);
    line-height: 20px;
  }
  .contact {
    list-style: none;
    margin: 17px 0 0;
    padding: 0;
    font-family: "Open Sans", sans-serif;
    font-size: 17px;
    color: var(--text);
  }
  .contact li {
    display: flex;
    align-items: center;
    height: 25.5px;
  }
  .contact svg { width: 15px; height: 15px; margin-right: 8px; flex: none; }

  .divider {
    position: absolute;
    left: 332px;
    top: 171px;
    width: 2px;
    height: 139px;
    background: var(--navy);
  }

  .services {
    position: absolute;
    left: 384px;
    top: 164px;
    list-style: none;
    margin: 0;
    padding: 0;
    font-family: "Open Sans", sans-serif;
    font-size: 18px;
    color: var(--text);
  }
  .services li {
    display: flex;
    align-items: center;
    height: 30.5px;
  }
  .services li::before {
    content: "";
    width: 8px;
    height: 8px;
    background: var(--blue-light);
    margin-right: 9px;
  }

  .offer {
    position: absolute;
    left: 0;
    top: 348px;
    width: 100%;
    margin: 0;
    text-align: center;
    font-family: "Open Sans", sans-serif;
    font-size: 17.5px;
    line-height: 22px;
    color: var(--text);
  }
</style>
</head>
<body>
<main class="canvas">
  <section class="card card--front" aria-label="Business card front">
    <div class="wordmark">VANTRELO</div>
    <div class="tagline">NUTRITION - FITNESS - HEALTH</div>
    <span class="side-band side-band--left"></span>
    <span class="side-band side-band--right"></span>

    <div class="person">
      <h1 class="person__name">DEREK FULHAM</h1>
      <p class="person__creds">BKin, CEP, RMT, NSCA-CPT, Pn1</p>
      <ul class="contact">
        <li>
          <svg viewBox="0 0 16 16" aria-hidden="true"><rect x="1" y="1" width="14" height="14" rx="2" fill="var(--navy)"/></svg>
          @derek_fulham
        </li>
        <li>
          <svg viewBox="0 0 16 16" aria-hidden="true"><rect x="1" y="3" width="14" height="10" fill="var(--navy)"/><path d="M1.5 3.5 8 9l6.5-5.5" stroke="#fff" stroke-width="1.3" fill="none"/></svg>
          derek@vantrelo.com
        </li>
        <li>
          <svg viewBox="0 0 16 16" aria-hidden="true"><circle cx="8" cy="8" r="6.5" fill="none" stroke="var(--navy)" stroke-width="1.6"/><path d="M1.5 8h13M8 1.5c-3 3.5-3 9.5 0 13M8 1.5c3 3.5 3 9.5 0 13" stroke="var(--navy)" stroke-width="1.2" fill="none"/></svg>
          www.vantrelo.com
        </li>
      </ul>
    </div>

    <span class="divider"></span>

    <ul class="services">
      <li>Personal Training</li>
      <li>Golf Fitness</li>
      <li>Injury Rehab</li>
      <li>Massage Therapy</li>
      <li>Yoga</li>
    </ul>

    <p class="offer">Contact us to receive a FREE assessment</p>
  </section>

  <section class="card card--back" aria-label="Business card back">
    <div class="wordmark">VANTRELO</div>
    <div class="tagline">NUTRITION - FITNESS - HEALTH</div>
  </section>
</main>
</body>
</html>
```